UX - Need some screens design for a Skill Assessment Application

I am building an app to carry out skill assessments. Depending on how the assessment is configured, it may have one or more parts
1. Question based assessment (Multiple Choice, True False, Fill in the blanks"
2. Endorsement by two colleagues - A screen that allows user to pick colleagues based on search and shows the status of pending requests
3. A written submission - a page that explains the format of the submission and a file upload
As each assessment can be configured with or without any of the steps, the assessment UI must be such that these areas get hidden/displayed based on configuration.
Colour codes to be used can be #0e78bb and #ffffff
There will also be a start screen (instructions) and an end screen (results)
Target Market(s)
Enterprise software
Number of Pages Required
4 page

```html
<!DOCTYPE html>
<html lang="en">
<head>
<meta charset="utf-8">
<title>Skill Assessment App – Screens</title>
<link href="https://fonts.googleapis.com/css2?family=Inter:wght@400;500;600;700&display=swap" rel="stylesheet">
<style>
:root{
  --board:#585b5e;
  --nav:#0b5dad;
  --primary:#0e78bb;
  --white:#ffffff;
  --ink:#1f2937;
  --muted:#6b7280;
  --line:#e5e7eb;
  --band:#f1f3f6;
  --soft:#f7f8fa;
  --pill:#e3f0fa;
  --teal-bg:#d7f3ec;
  --teal:#1a9a7c;
  --skin:#c9a58a;
}
*{box-sizing:border-box;margin:0;padding:0}
html,body{width:1200px;height:1200px;overflow:hidden}
body{background:var(--board);font-family:'Inter',sans-serif;color:var(--ink);position:relative}
.col-title{position:absolute;top:64px;width:386px;text-align:center;color:var(--white);font-size:13px;font-weight:700;letter-spacing:.3px}
.screen{position:absolute;width:336px;height:191px;overflow:hidden;background:var(--white)}
.frame{width:541px;height:308px;transform:scale(.6211);transform-origin:0 0;position:relative;font-size:4.6px;line-height:1.2}
.abs{position:absolute}
.nav{height:19px;background:var(--nav);display:flex;align-items:center;padding:0 25px;color:var(--white)}
.brand{font-size:5.6px;font-weight:500;display:flex;gap:4px;align-items:center}
.brand-mark{width:8px;height:8px;background:var(--white);border-radius:50%}
.menu{margin-left:auto;display:flex;gap:9px;font-size:4.4px;opacity:.85}
.menu .on{font-weight:700;opacity:1}
.me{width:10px;height:10px;border-radius:50%;background:var(--skin);margin-left:9px;border:1px solid var(--white)}
.caret{margin-left:3px;width:4px;height:4px}
.crumb{font-size:3.8px;color:var(--muted);white-space:nowrap}
.crumb b{color:var(--primary);font-weight:400}
.h1{font-size:9.5px;font-weight:600;white-space:nowrap}
.sub{font-size:4.4px;color:var(--muted)}
.btn{display:inline-flex;align-items:center;justify-content:center;gap:3px;border-radius:2px;font-size:4.2px;height:12px;padding:0 7px;white-space:nowrap}
.btn.solid{background:var(--primary);color:var(--white)}
.btn.line{border:.8px solid var(--primary);color:var(--primary);background:var(--white)}
.tabs{display:flex;gap:0;border-bottom:.6px solid var(--line);font-size:4.8px;color:var(--muted)}
.tabs span{padding:0 16px 5px 0;width:60px;white-space:nowrap}
.tabs .on{color:var(--primary);border-bottom:1px solid var(--primary)}
.refresh{font-size:4.2px;color:var(--primary)}
.card{border:.8px solid var(--line);border-radius:2px;background:var(--white)}
.row{display:grid;align-items:center;border-bottom:.6px solid var(--line);padding:0 9px}
.row>span{white-space:nowrap;overflow:hidden}
.row.head{background:#f9fafb;font-weight:600;font-size:4.2px;color:#374151}
.link{color:var(--primary)}
.badge{display:inline-block;border-radius:6px;padding:1.5px 5px;font-size:3.8px;background:var(--pill);color:var(--primary);white-space:nowrap}
.badge.teal{background:var(--teal-bg);color:var(--teal)}
.dots{font-size:7px;line-height:0;color:#4b5563;text-align:center;overflow:visible!important}
.pager{display:flex;justify-content:center;gap:4px;font-size:3.8px}
.pager span{height:11px;min-width:11px;display:flex;align-items:center;justify-content:center;border:.6px solid var(--line);border-radius:2px;color:#9ca3af;padding:0 6px;white-space:nowrap}
.pager .cur{background:var(--primary);border-color:var(--primary);color:var(--white);padding:0}
.pager .plain{border:0;color:var(--ink);padding:0}
.av{width:8px;height:8px;border-radius:50%;display:inline-block;background:var(--skin);flex:none}
.av.d{background:#6b5b52}.av.l{background:#e2b98d}.av.g{background:#9ca3af}
.back-ico{width:7px;height:7px;border:.8px solid var(--primary);border-radius:50%;display:inline-block;vertical-align:middle;margin-right:4px}
.title-ico{width:8px;height:8px;border:.8px solid #4b5563;border-radius:1px;display:inline-block;margin-right:5px;vertical-align:-1px}
.band{left:0;right:0;background:var(--band);font-size:3.6px;color:#4b5563;display:flex;align-items:center;padding:0 40px;white-space:nowrap}
.band b{font-weight:400;color:var(--primary)}
.ring{width:10px;height:10px;border-radius:50%;border:1.5px solid var(--primary);border-left-color:#d1d5db;margin-left:auto;flex:none}
.body-soft{left:0;right:0;bottom:0;background:var(--soft)}
.q{font-size:5.4px;font-weight:500;white-space:nowrap}
.opt{height:28px;background:var(--white);border:.6px solid #eef0f3;border-radius:2px;display:flex;align-items:center;gap:9px;padding:0 7px;font-size:4px;color:#4b5563;margin-bottom:6px;white-space:nowrap}
.opt i{width:10px;height:10px;background:var(--pill);color:var(--primary);font-style:normal;display:flex;align-items:center;justify-content:center;font-size:4px;flex:none}
.opt.sel{border:.8px solid var(--primary);color:var(--primary);background:#f5fafd}
.tf{margin-left:auto;display:flex;gap:3px}
.tf span{height:10px;padding:0 6px;border-radius:5px;border:.6px solid var(--line);display:flex;align-items:center;font-size:3.8px;color:var(--primary);background:var(--white)}
.tf .on{background:var(--primary);color:var(--white);border-color:var(--primary)}
.skip{font-size:4px;color:#4b5563;white-space:nowrap}
.filter{font-size:3.4px;color:#4b5563;white-space:nowrap}
.field{height:11px;border:.6px solid #d1d5db;border-radius:2px;background:var(--white);display:flex;align-items:center;padding:0 5px;font-size:3.8px;margin-top:2px}
.tag{font-size:3.2px;border:.5px solid var(--line);border-radius:2px;padding:1px 3px;margin-right:2px;color:var(--muted);font-style:normal}
.chk{width:5px;height:5px;border:.5px solid #cbd5e1;border-radius:1px;display:inline-block}
.chk.on{background:var(--primary);border-color:var(--primary)}
.av-stack{display:flex;gap:1px;justify-content:flex-end;align-items:center}
.go{width:9px;height:9px;border-radius:50%;background:var(--primary);margin-left:4px;flex:none}
.blank{display:inline-block;border-bottom:.6px solid #d1d5db;width:60px;color:#cbd5e1;margin:0 4px}
</style>
</head>
<body>

<div class="col-title" style="left:21px">01 - ASSESSMENTS SCREEN</div>
<div class="col-title" style="left:407px">02 - ENDORSEMENT SCREEN</div>
<div class="col-title" style="left:793px">03 - SUBMISSION SCREEN</div>

<!-- ===== Assessments list ===== -->
<section class="screen" style="left:46px;top:106px"><div class="frame">
  <header class="nav"><span class="brand"><i class="brand-mark"></i>LogoPlaceholder</span><div class="menu"><span class="on">Assessments</span><span>Endorsement</span><span>Submissions</span><span>Results</span></div><span class="me" role="img" aria-label="User profile photo"></span><svg class="caret" viewBox="0 0 4 4"><path d="M.5 1.2 2 2.7 3.5 1.2" stroke="#fff" stroke-width=".6" fill="none"/></svg></header>
  <div class="abs crumb" style="left:32px;top:30px">Assessment /</div>
  <div class="abs h1" style="left:32px;top:42px">Assessments</div>
  <div class="abs sub" style="left:32px;top:58px">Here are the complete details of assessments.</div>
  <span class="abs btn solid" style="left:429px;top:47px;width:80px">▣ Create New Assessment</span>
  <div class="abs tabs" style="left:32px;top:75px;width:477px"><span class="on">Active (6)</span><span>Draft (2)</span><span>Completed (3)</span></div>
  <div class="abs refresh" style="right:32px;top:75px">↻ Refresh</div>
  <div class="abs card" style="left:32px;top:98px;width:477px;height:190px">
    <div class="row head" style="grid-template-columns:33px 109px 64px 77px 81px 78px 1fr;height:18px"><span>S.No</span><span>Assessment</span><span>Published On</span><span>Start Time</span><span>End Time</span><span>Status</span><span style="text-align:right">Actions</span></div>
    <div class="row" style="grid-template-columns:33px 109px 64px 77px 81px 78px 1fr;height:24.3px"><span>&nbsp;1</span><span class="link">Application Design Capabilities</span><span>23/08/2023</span><span>24/09/2023 9:00 AM</span><span>24/09/2024 9:00 AM</span><span><i class="badge">In Progress</i>&nbsp; 4/8</span><span class="dots">⋮</span></div>
    <div class="row" style="grid-template-columns:33px 109px 64px 77px 81px 78px 1fr;height:24.3px"><span>&nbsp;2</span><span class="link">UI/UX Designer</span><span>17/08/2023</span><span>18/09/2023 9:00 AM</span><span>18/09/2024 9:00 AM</span><span><i class="badge teal">Yet to Start</i>&nbsp; 10/10</span><span class="dots">⋮</span></div>
    <div class="row" style="grid-template-columns:33px 109px 64px 77px 81px 78px 1fr;height:24.3px"><span>&nbsp;3</span><span class="link">Front-end Developer</span><span>08/09/2023</span><span>09/09/2023 9:00 AM</span><span>09/09/2024 9:00 AM</span><span><i class="badge teal">Yet to Start</i>&nbsp; 10/10</span><span class="dots">⋮</span></div>
    <div class="row" style="grid-template-columns:33px 109px 64px 77px 81px 78px 1fr;height:24.3px"><span>&nbsp;4</span><span class="link">Cybersecurity Analyst</span><span>11/07/2023</span><span>12/07/2023 9:00 AM</span><span>12/07/2024 9:00 AM</span><span><i class="badge">In Progress</i>&nbsp; 8/10</span><span class="dots">⋮</span></div>
    <div class="row" style="grid-template-columns:33px 109px 64px 77px 81px 78px 1fr;height:24.3px"><span>&nbsp;5</span><span class="link">DevOps Engineer</span><span>22/02/2024</span><span>23/02/2024 9:00 AM</span><span>23/02/2025 9:00 AM</span><span><i class="badge teal">Yet to Start</i>&nbsp; 10/10</span><span class="dots">⋮</span></div>
    <div class="row" style="grid-template-columns:33px 109px 64px 77px 81px 78px 1fr;height:24.3px"><span>&nbsp;6</span><span class="link">Sales Representative</span><span>15/05/2024</span><span>16/05/2024 9:00 AM</span><span>16/05/2025 9:00 AM</span><span><i class="badge">In Progress</i>&nbsp; 2/10</span><span class="dots">⋮</span></div>
    <div class="pager" style="margin-top:7px"><span>‹ Back</span><span class="cur">1</span><span>Next ›</span></div>
  </div>
</div></section>

<!-- ===== Question: multiple choice ===== -->
<section class="screen" style="left:46px;top:315px"><div class="frame">
  <header class="nav"><span class="brand"><i class="brand-mark"></i>LogoPlaceholder</span><div class="menu"><span class="on">Assessments</span><span>Endorsement</span><span>Submissions</span><span>Results</span></div><span class="me" role="img" aria-label="User profile photo"></span><svg class="caret" viewBox="0 0 4 4"><path d="M.5 1.2 2 2.7 3.5 1.2" stroke="#fff" stroke-width=".6" fill="none"/></svg></header>
  <div class="abs crumb" style="left:25px;top:29px"><i class="back-ico"></i><b>Assessment</b> / Application Design Capabilities</div>
  <div class="abs crumb" style="right:40px;top:30px">Last Updated: 17/05/2024</div>
  <div class="abs h1" style="left:40px;top:44px"><i class="title-ico"></i>Application Design Capabilities</div>
  <span class="abs btn line" style="left:455px;top:43px;width:46px">Save Progress</span>
  <div class="abs body-soft" style="top:82px"></div>
  <div class="abs band" style="top:66px;height:16px"><span>Assessment Date: <b>September 23, 2024</b></span><span style="margin-left:19px">Assessment Type: <b>UI/UX Skill</b></span><span style="margin-left:19px">Assessment Responses: 4 of 8 Responded / Closed: in next 4 month</span><i class="ring"></i><span style="margin-left:3px">5 / 8</span></div>
  <div class="abs" style="left:165px;top:98px;width:212px">
    <div class="q">Q.5.&nbsp;&nbsp; What's your knowledge regarding User Interface?</div>
    <div style="margin-top:10px">
      <div class="opt"><i>1</i>Lorem ipsum dolor sit amet, consecteteur adispiscing elit.</div>
      <div class="opt"><i>2</i>Lorem ipsum dolor sit amet, consecteteur adispiscing elit.</div>
      <div class="opt sel"><i>3</i>Lorem ipsum dolor sit amet, consecteteur adispiscing elit.</div>
      <div class="opt"><i>4</i>Lorem ipsum dolor sit amet, consecteteur adispiscing elit.</div>
    </div>
  </div>
  <span class="abs btn line" style="left:165px;top:277px;width:32px">Go Back</span>
  <span class="abs skip" style="left:326px;top:281px">Skip ›</span>
  <span class="abs btn solid" style="left:353px;top:277px;width:24px">Next</span>
</div></section>

<!-- ===== Question: multiple T/F ===== -->
<section class="screen" style="left:46px;top:524px"><div class="frame">
  <header class="nav"><span class="brand"><i class="brand-mark"></i>LogoPlaceholder</span><div class="menu"><span class="on">Assessments</span><span>Endorsement</span><span>Submissions</span><span>Results</span></div><span class="me" role="img" aria-label="User profile photo"></span><svg class="caret" viewBox="0 0 4 4"><path d="M.5 1.2 2 2.7 3.5 1.2" stroke="#fff" stroke-width=".6" fill="none"/></svg></header>
  <div class="abs crumb" style="left:25px;top:29px"><i class="back-ico"></i><b>Assessment</b> / Application Design Capabilities</div>
  <div class="abs crumb" style="right:40px;top:30px">Last Updated: 17/05/2024</div>
  <div class="abs h1" style="left:40px;top:44px"><i class="title-ico"></i>Application Design Capabilities</div>
  <span class="abs btn line" style="left:455px;top:43px;width:46px">Save Progress</span>
  <div class="abs body-soft" style="top:82px"></div>
  <div class="abs band" style="top:66px;height:16px"><span>Assessment Date: <b>September 23, 2024</b></span><span style="margin-left:19px">Assessment Type: <b>UI/UX Skill</b></span><span style="margin-left:19px">Assessment Responses: 5 of 8 Responded / Closed: in next 4 month</span><i class="ring"></i><span style="margin-left:3px">6 / 8</span></div>
  <div class="abs" style="left:165px;top:98px;width:212px">
    <div class="q">Q.6.&nbsp;&nbsp; This is multiple question with T/F choice</div>
    <div style="margin-top:10px">
      <div class="opt"><i>1</i>Lorem ipsum dolor sit amet?<span class="tf"><span class="on">True</span><span>False</span></span></div>
      <div class="opt"><i>2</i>Lorem ipsum dolor sit amet?<span class="tf"><span>True</span><span class="on">False</span></span></div>
      <div class="opt"><i>3</i>Lorem ipsum dolor sit amet?<span class="tf"><span class="on">True</span><span>False</span></span></div>
    </div>
  </div>
  <span class="abs btn line" style="left:165px;top:243px;width:32px">Go Back</span>
  <span class="abs skip" style="left:326px;top:247px">Skip ›</span>
  <span class="abs btn solid" style="left:353px;top:243px;width:24px">Next</span>
</div></section>

<!-- ===== Question: single T/F ===== -->
<section class="screen" style="left:46px;top:733px"><div class="frame">
  <header class="nav"><span class="brand"><i class="brand-mark"></i>LogoPlaceholder</span><div class="menu"><span class="on">Assessments</span><span>Endorsement</span><span>Submissions</span><span>Results</span></div><span class="me" role="img" aria-label="User profile photo"></span><svg class="caret" viewBox="0 0 4 4"><path d="M.5 1.2 2 2.7 3.5 1.2" stroke="#fff" stroke-width=".6" fill="none"/></svg></header>
  <div class="abs crumb" style="left:25px;top:29px"><i class="back-ico"></i><b>Assessment</b> / Application Design Capabilities</div>
  <div class="abs crumb" style="right:40px;top:30px">Last Updated: 17/05/2024</div>
  <div class="abs h1" style="left:40px;top:44px"><i class="title-ico"></i>Application Design Capabilities</div>
  <span class="abs btn line" style="left:455px;top:43px;width:46px">Save Progress</span>
  <div class="abs body-soft" style="top:82px"></div>
  <div class="abs band" style="top:66px;height:16px"><span>Assessment Date: <b>September 23, 2024</b></span><span style="margin-left:19px">Assessment Type: <b>UI/UX Skill</b></span><span style="margin-left:19px">Assessment Responses: 6 of 8 Responded / Closed: in next 4 month</span><i class="ring"></i><span style="margin-left:3px">7 / 8</span></div>
  <div class="abs" style="left:165px;top:98px;width:212px">
    <div class="q">Q.7.&nbsp;&nbsp; This is a single question with T/F choice</div>
    <div class="tf" style="margin:9px 0 0 14px;justify-content:flex-start"><span class="on">True</span><span>False</span></div>
  </div>
  <span class="abs btn line" style="left:165px;top:157px;width:32px">Go Back</span>
  <span class="abs skip" style="left:326px;top:161px">Skip ›</span>
  <span class="abs btn solid" style="left:353px;top:157px;width:24px">Next</span>
</div></section>

<!-- ===== Question: fill in blanks ===== -->
<section class="screen" style="left:46px;top:943px"><div class="frame">
  <header class="nav"><span class="brand"><i class="brand-mark"></i>LogoPlaceholder</span><div class="menu"><span class="on">Assessments</span><span>Endorsement</span><span>Submissions</span><span>Results</span></div><span class="me" role="img" aria-label="User profile photo"></span><svg class="caret" viewBox="0 0 4 4"><path d="M.5 1.2 2 2.7 3.5 1.2" stroke="#fff" stroke-width=".6" fill="none"/></svg></header>
  <div class="abs crumb" style="left:25px;top:29px"><i class="back-ico"></i><b>Assessment</b> / Application Design Capabilities</div>
  <div class="abs crumb" style="right:40px;top:30px">Last Updated: 17/05/2024</div>
  <div class="abs h1" style="left:40px;top:44px"><i class="title-ico"></i>Application Design Capabilities</div>
  <span class="abs btn line" style="left:455px;top:43px;width:46px">Save Progress</span>
  <div class="abs body-soft" style="top:82px"></div>
  <div class="abs band" style="top:66px;height:16px"><span>Assessment Date: <b>September 23, 2024</b></span><span style="margin-left:19px">Assessment Type: <b>UI/UX Skill</b></span><span style="margin-left:19px">Assessment Responses: 7 of 8 Responded / Closed: in next 4 month</span><i class="ring" style="border-left-color:var(--primary)"></i><span style="margin-left:3px">8 / 8</span></div>
  <div class="abs q" style="left:165px;top:98px;width:212px;line-height:21px">
    <div>Q.8.&nbsp;&nbsp; How do you<span class="blank">Type a label</span>&nbsp;&nbsp;in<span class="blank">Type a label</span></div>
    <div style="padding-left:21px">This is a fill in the<span class="blank" style="width:55px">blanks</span>&nbsp; field. Please</div>
    <div style="padding-left:21px">sign your name:<span class="blank" style="width:70px">here</span>. Thank you</div>
  </div>
  <span class="abs btn line" style="left:165px;top:181px;width:32px">Go Back</span>
  <span class="abs btn solid" style="left:328px;top:181px;width:49px">Submit Answer</span>
</div></section>

<!-- ===== Endorsement list ===== -->
<section class="screen" style="left:432px;top:106px"><div class="frame">
  <header class="nav"><span class="brand"><i class="brand-mark"></i>LogoPlaceholder</span><div class="menu"><span>Assessments</span><span class="on">Endorsement</span><span>Submissions</span><span>Results</span></div><span class="me" role="img" aria-label="User profile photo"></span><svg class="caret" viewBox="0 0 4 4"><path d="M.5 1.2 2 2.7 3.5 1.2" stroke="#fff" stroke-width=".6" fill="none"/></svg></header>
  <div class="abs crumb" style="left:32px;top:30px">Assessment /</div>
  <div class="abs h1" style="left:32px;top:42px">Endorsement</div>
  <div class="abs sub" style="left:32px;top:58px">Here are the complete details of assessments.</div>
  <span class="abs btn solid" style="left:435px;top:47px;width:74px">⤒ Request Endorsement</span>
  <div class="abs tabs" style="left:32px;top:75px;width:477px"><span class="on" style="width:40px">All (3)</span><span>Pending (2)</span></div>
  <div class="abs refresh" style="right:32px;top:75px">↻ Refresh</div>
  <div class="abs card" style="left:32px;top:102px;width:477px;height:126px">
    <div class="row head" style="grid-template-columns:100px 51px 56px 80px 89px 1fr;height:18px"><span>Endorsements Category</span><span>Date Request</span><span>Effective Date</span><span>Endorsement</span><span>Skill &amp; Expertise</span><span>Status</span></div>
    <div class="row" style="grid-template-columns:100px 51px 56px 80px 89px 1fr;height:27px"><span>Application Design Capabilities</span><span>23/02/2024</span><span>29/02/2024</span><span style="display:flex;gap:4px;align-items:center"><i class="av" role="img" aria-label="Colleague photo"></i><b class="link" style="font-weight:400">Mei Lin Tan</b></span><span>Senior Web Designer<br><b class="link" style="font-weight:400;font-size:3.6px">▢ Fenwick Industries Ltd.</b></span><span style="display:flex;align-items:center"><i class="badge">Pending</i><i class="btn line" style="margin-left:auto;font-style:normal;height:11px">Cancel Request</i></span></div>
    <div class="row" style="grid-template-columns:100px 51px 56px 80px 89px 1fr;height:27px"><span>UI/UX Designer</span><span>23/02/2024</span><span>29/02/2024</span><span style="display:flex;gap:4px;align-items:center"><i class="av d" role="img" aria-label="Colleague photo"></i><b class="link" style="font-weight:400">Robin Clarke</b></span><span>UX Researcher<br><b class="link" style="font-weight:400;font-size:3.6px">▢ Brightcode Corp.</b></span><span style="display:flex;align-items:center"><i class="badge">Pending</i><i class="btn line" style="margin-left:auto;font-style:normal;height:11px">Cancel Request</i></span></div>
    <div class="row" style="grid-template-columns:100px 51px 56px 80px 89px 1fr;height:27px"><span>Front-end Developer</span><span>12/01/2024</span><span>17/01/2024</span><span style="display:flex;gap:4px;align-items:center"><i class="av g" role="img" aria-label="Colleague photo"></i><b class="link" style="font-weight:400">Rowan Marks Jr.</b></span><span>Lead Programmer<br><b class="link" style="font-weight:400;font-size:3.6px">▢ Brightcode Corp.</b></span><span style="display:flex;align-items:center;overflow:visible"><i class="badge teal">Approved</i><i class="dots" style="margin-left:auto;margin-right:16px;font-style:normal">⋮</i></span></div>
    <div class="pager" style="margin-top:8px"><span>‹ Back</span><span class="cur">1</span><span>Next ›</span></div>
  </div>
</div></section>

<!-- ===== New endorsement request ===== -->
<section class="screen" style="left:432px;top:315px"><div class="frame">
  <header class="nav"><span class="brand"><i class="brand-mark"></i>LogoPlaceholder</span><div class="menu"><span>Assessments</span><span class="on">Endorsement</span><span>Submissions</span><span>Results</span></div><span class="me" role="img" aria-label="User profile photo"></span><svg class="caret" viewBox="0 0 4 4"><path d="M.5 1.2 2 2.7 3.5 1.2" stroke="#fff" stroke-width=".6" fill="none"/></svg></header>
  <div class="abs crumb" style="left:25px;top:29px"><i class="back-ico"></i><b>Endorsement</b> / New Endorsement Request</div>
  <div class="abs h1" style="left:40px;top:44px"><i class="title-ico"></i>New Endorsement Request</div>
  <div class="abs" style="left:0;right:0;top:64px;height:.6px;background:var(--line)"></div>
  <div class="abs body-soft" style="top:65px"></div>
  <div class="abs card" style="left:39px;top:73px;width:461px;height:183px">
    <div class="row head" style="grid-template-columns:25px 1fr 80px;height:17px"><span>User</span><span>Endorsements Category</span><span style="text-align:right">Endorsements</span></div>
    <div class="row" style="grid-template-columns:25px 1fr 230px;height:27.4px"><span>24</span><span>Application Design Capabilities</span><span class="av-stack" role="img" aria-label="Colleague photos"><i class="av"></i><i class="av d"></i><i class="av g"></i><i class="av l"></i><i class="av"></i><i class="av d"></i><i class="av l"></i><i class="av g"></i><i class="av"></i><i class="av d"></i><i class="av"></i><i class="av l"></i><i class="av g" style="font-style:normal;font-size:3px;text-align:center;line-height:8px">11+</i><i class="av"></i><i class="go"></i></span></div>
    <div class="row" style="grid-template-columns:25px 1fr 230px;height:27.4px"><span>8</span><span>UI/UX Designer</span><span class="av-stack" role="img" aria-label="Colleague photos"><i class="av d"></i><i class="av g"></i><i class="av"></i><i class="av l"></i><i class="av d"></i><i class="av l"></i><i class="av"></i><i class="av g"></i><i class="go"></i></span></div>
    <div class="row" style="grid-template-columns:25px 1fr 230px;height:27.4px"><span>6</span><span>Front-end Developer</span><span class="av-stack" role="img" aria-label="Colleague photos"><i class="av d"></i><i class="av g"></i><i class="av l"></i><i class="av"></i><i class="av d"></i><i class="av"></i><i class="go"></i></span></div>
    <div class="row" style="grid-template-columns:25px 1fr 230px;height:27.4px"><span>11</span><span>Cybersecurity Analyst</span><span class="av-stack" role="img" aria-label="Colleague photos"><i class="av"></i><i class="av d"></i><i class="av l"></i><i class="av g"></i><i class="av"></i><i class="av d"></i><i class="av d"></i><i class="av"></i><i class="av g"></i><i class="av l"></i><i class="av"></i><i class="go"></i></span></div>
    <div class="row" style="grid-template-columns:25px 1fr 230px;height:27.4px"><span>8</span><span>DevOps Engineer</span><span class="av-stack" role="img" aria-label="Colleague photos"><i class="av l"></i><i class="av g"></i><i class="av d"></i><i class="av"></i><i class="av g"></i><i class="av d"></i><i class="av"></i><i class="av l"></i><i class="go"></i></span></div>
    <div class="row" style="grid-template-columns:25px 1fr 230px;height:27.4px;border-bottom:0"><span>4</span><span>Sales Representative</span><span class="av-stack" role="img" aria-label="Colleague photos"><i class="av"></i><i class="av g"></i><i class="av d"></i><i class="av l"></i><i class="go"></i></span></div>
  </div>
</div></section>

<!-- ===== Endorsement pick colleagues (3 states) ===== -->
<section class="screen" style="left:432px;top:524px"><div class="frame">
  <header class="nav"><span class="brand"><i class="brand-mark"></i>LogoPlaceholder</span><div class="menu"><span>Assessments</span><span class="on">Endorsement</span><span>Submissions</span><span>Results</span></div><span class="me" role="img" aria-label="User profile photo"></span><svg class="caret" viewBox="0 0 4 4"><path d="M.5 1.2 2 2.7 3.5 1.2" stroke="#fff" stroke-width=".6" fill="none"/></svg></header>
  <div class="abs crumb" style="left:25px;top:29px"><i class="back-ico"></i><b>Endorsement</b> / <b>New Endorsement Request</b> / Application Design Capabilities</div>
  <div class="abs h1" style="left:40px;top:44px"><i class="title-ico"></i>Application Design Capabilities</div>
  <div class="abs" style="left:0;right:0;top:63px;height:25px;background:var(--band)"></div>
  <div class="abs filter" style="left:39px;top:68px;width:135px">Choose Category<div class="field">Application Design Capabilities (24)<span style="margin-left:auto">⌄</span></div></div>
  <div class="abs filter" style="left:181px;top:68px;width:76px">Effective Date<div class="field">Select date<span style="margin-left:auto">⌄</span></div></div>
  <div class="abs filter" style="left:264px;top:68px;width:130px">Endorsement<div class="field" style="color:#9ca3af">Search<span style="margin-left:auto">⌕</span></div></div>
  <div class="abs filter" style="right:41px;top:78px;color:#9fc3dd">Send Endorsement Request</div>
  <div class="abs body-soft" style="top:88px"></div>
  <div class="abs card" style="left:39px;top:102px;width:461px;height:190px">
    <div class="row head" style="grid-template-columns:10px 87px 160px 87px 1fr;height:17px"><i class="chk"></i><span>Endorsements</span><span>Skill &amp; Expertise</span><span>Role</span><span>Company</span></div>
    <div class="row" style="grid-template-columns:10px 87px 160px 87px 1fr 22px;height:20.5px"><i class="chk"></i><span style="display:flex;gap:4px;align-items:center"><i class="av" role="img" aria-label="Colleague photo"></i>Mei Lin Tan</span><span><i class="tag">UI</i><i class="tag">UX</i><i class="tag">Wireframe</i><i class="tag">Concept Design</i><i class="tag">Prototype</i></span><span>Fenwick Industries Ltd.</span><span class="link">Fenwick Industries Ltd.</span><i class="btn line" style="font-style:normal;height:10px;padding:0 5px">Add</i></div>
    <div class="row" style="grid-template-columns:10px 87px 160px 87px 1fr 22px;height:20.5px"><i class="chk"></i><span style="display:flex;gap:4px;align-items:center"><i class="av d" role="img" aria-label="Colleague photo"></i>Harold Dunne</span><span><i class="tag">Concept Design</i><i class="tag">Prototype</i></span><span>Brightcode Corp.</span><span class="link">Brightcode Corp.</span><i class="btn line" style="font-style:normal;height:10px;padding:0 5px">Add</i></div>
    <div class="row" style="grid-template-columns:10px 87px 160px 87px 1fr 22px;height:20.5px"><i class="chk"></i><span style="display:flex;gap:4px;align-items:center"><i class="av g" role="img" aria-label="Colleague photo"></i>Marcus Tolland</span><span><i class="tag">UI</i><i class="tag">Design Analytic</i></span><span>Brightcode Corp.</span><span class="link">Brightcode Corp.</span><i class="btn line" style="font-style:normal;height:10px;padding:0 5px">Add</i></div>
    <div class="row" style="grid-template-columns:10px 87px 160px 87px 1fr 22px;height:20.5px"><i class="chk"></i><span style="display:flex;gap:4px;align-items:center"><i class="av l" role="img" aria-label="Colleague photo"></i>Alina Kerr</span><span><i class="tag">Wireframe</i><i class="tag">Concept Design</i><i class="tag">Prototype</i></span><span>Brightcode Corp.</span><span class="link">Brightcode Corp.</span><i class="btn line" style="font-style:normal;height:10px;padding:0 5px">Add</i></div>
    <div class="row" style="grid-template-columns:10px 87px 160px 87px 1fr 22px;height:20.5px"><i class="chk"></i><span style="display:flex;gap:4px;align-items:center"><i class="av" role="img" aria-label="Colleague photo"></i>Rowan Marks Jr.</span><span><i class="tag">UX</i><i class="tag">Concept Design</i></span><span>Brightcode Corp.</span><span class="link">Brightcode Corp.</span><i class="btn line" style="font-style:normal;height:10px;padding:0 5px">Add</i></div>
    <div class="row" style="grid-template-columns:10px 87px 160px 87px 1fr 22px;height:20.5px"><i class="chk"></i><span style="display:flex;gap:4px;align-items:center"><i class="av d" role="img" aria-label="Colleague photo"></i>Dimas R. Prakoso</span><span><i class="tag">Design Analytic</i><i class="tag">Wireframe</i></span><span>Inkara Studio</span><span class="link">Inkara Studio</span><i class="btn line" style="font-style:normal;height:10px;padding:0 5px">Add</i></div>
    <div class="row" style="grid-template-columns:10px 87px 160px 87px 1fr 22px;height:20.5px;border-bottom:0"><i class="chk"></i><span style="display:flex;gap:4px;align-items:center"><i class="av g" role="img" aria-label="Colleague photo"></i>Robin Clarke</span><span><i class="tag">Wireframe</i><i class="tag">UX</i><i class="tag">Concept Design</i><i class="tag">UI</i></span><span>Brightcode Corp.</span><span class="link">Brightcode Corp.</span><i class="btn line" style="font-style:normal;height:10px;padding:0 5px">Add</i></div>
    <div class="pager" style="margin-top:5px"><span>‹ Back</span><span class="cur">1</span><span class="plain">2</span><span>Next ›</span></div>
  </div>
</div></section>

<section class="screen" style="left:432px;top:733px"><div class="frame">
  <header class="nav"><span class="brand"><i class="brand-mark"></i>LogoPlaceholder</span><div class="menu"><span>Assessments</span><span class="on">Endorsement</span><span>Submissions</span><span>Results</span></div><span class="me" role="img" aria-label="User profile photo"></span><svg class="caret" viewBox="0 0 4 4"><path d="M.5 1.2 2 2.7 3.5 1.2" stroke="#fff" stroke-width=".6" fill="none"/></svg></header>
  <div class="abs crumb" style="left:25px;top:29px"><i class="back-ico"></i><b>Endorsement</b> / <b>New Endorsement Request</b> / Application Design Capabilities</div>
  <div class="abs h1" style="left:40px;top:44px"><i class="title-ico"></i>Application Design Capabilities</div>
  <div class="abs" style="left:0;right:0;top:63px;height:25px;background:var(--band)"></div>
  <div class="abs filter" style="left:39px;top:68px;width:135px">Choose Category<div class="field">Application Design Capabilities (24)<span style="margin-left:auto">⌄</span></div></div>
  <div class="abs filter" style="left:181px;top:68px;width:76px">Effective Date<div class="field">Select date<span style="margin-left:auto">⌄</span></div></div>
  <div class="abs filter" style="left:264px;top:68px;width:130px">Endorsement<div class="field" style="color:#9ca3af">Search<span style="margin-left:auto">⌕</span></div></div>
  <div class="abs filter" style="right:41px;top:78px;color:#9fc3dd">Send Endorsement Request</div>
  <div class="abs body-soft" style="top:88px"></div>
  <div class="abs card" style="left:39px;top:102px;width:461px;height:190px">
    <div class="row head" style="grid-template-columns:10px 87px 160px 87px 1fr;height:17px"><i class="chk"></i><span>Endorsements</span><span>Skill &amp; Expertise</span><span>Role</span><span>Company</span></div>
    <div class="row" style="grid-template-columns:10px 87px 160px 87px 1fr 22px;height:20.5px"><i class="chk"></i><span style="display:flex;gap:4px;align-items:center"><i class="av" role="img" aria-label="Colleague photo"></i>Mei Lin Tan</span><span><i class="tag">UI</i><i class="tag">UX</i><i class="tag">Wireframe</i><i class="tag">Concept Design</i><i class="tag">Prototype</i></span><span>Fenwick Industries Ltd.</span><span class="link">Fenwick Industries Ltd.</span><i class="btn line" style="font-style:normal;height:10px;padding:0 5px">Add</i></div>
    <div class="row" style="grid-template-columns:10px 87px 160px 81px 1fr 28px;height:20.5px"><i class="chk"></i><span style="display:flex;gap:4px;align-items:center"><i class="av d" role="img" aria-label="Colleague photo"></i>Harold Dunne</span><span><i class="tag">Concept Design</i><i class="tag">Prototype</i></span><span>Brightcode Corp.</span><span class="link">Brightcode Corp.</span><i class="btn solid" style="font-style:normal;height:10px;padding:0 5px">Cancel</i></div>
    <div class="row" style="grid-template-columns:10px 87px 160px 87px 1fr 22px;height:20.5px"><i class="chk"></i><span style="display:flex;gap:4px;align-items:center"><i class="av g" role="img" aria-label="Colleague photo"></i>Marcus Tolland</span><span><i class="tag">UI</i><i class="tag">Design Analytic</i></span><span>Brightcode Corp.</span><span class="link">Brightcode Corp.</span><i class="btn line" style="font-style:normal;height:10px;padding:0 5px">Add</i></div>
    <div class="row" style="grid-template-columns:10px 87px 160px 87px 1fr 22px;height:20.5px"><i class="chk"></i><span style="display:flex;gap:4px;align-items:center"><i class="av l" role="img" aria-label="Colleague photo"></i>Alina Kerr</span><span><i class="tag">Wireframe</i><i class="tag">Concept Design</i><i class="tag">Prototype</i></span><span>Brightcode Corp.</span><span class="link">Brightcode Corp.</span><i class="btn line" style="font-style:normal;height:10px;padding:0 5px">Add</i></div>
    <div class="row" style="grid-template-columns:10px 87px 160px 87px 1fr 22px;height:20.5px"><i class="chk"></i><span style="display:flex;gap:4px;align-items:center"><i class="av" role="img" aria-label="Colleague photo"></i>Rowan Marks Jr.</span><span><i class="tag">UX</i><i class="tag">Concept Design</i></span><span>Brightcode Corp.</span><span class="link">Brightcode Corp.</span><i class="btn line" style="font-style:normal;height:10px;padding:0 5px">Add</i></div>
    <div class="row" style="grid-template-columns:10px 87px 160px 87px 1fr 22px;height:20.5px"><i class="chk"></i><span style="display:flex;gap:4px;align-items:center"><i class="av d" role="img" aria-label="Colleague photo"></i>Dimas R. Prakoso</span><span><i class="tag">Design Analytic</i><i class="tag">Wireframe</i></span><span>Inkara Studio</span><span class="link">Inkara Studio</span><i class="btn line" style="font-style:normal;height:10px;padding:0 5px">Add</i></div>
    <div class="row" style="grid-template-columns:10px 87px 160px 87px 1fr 22px;height:20.5px;border-bottom:0"><i class="chk"></i><span style="display:flex;gap:4px;align-items:center"><i class="av g" role="img" aria-label="Colleague photo"></i>Robin Clarke</span><span><i class="tag">Wireframe</i><i class="tag">UX</i><i class="tag">Concept Design</i><i class="tag">UI</i></span><span>Brightcode Corp.</span><span class="link">Brightcode Corp.</span><i class="btn line" style="font-style:normal;height:10px;padding:0 5px">Add</i></div>
    <div class="pager" style="margin-top:5px"><span>‹ Back</span><span class="cur">1</span><span class="plain">2</span><span>Next ›</span></div>
  </div>
</div></section>

<section class="screen" style="left:432px;top:943px"><div class="frame">
  <header class="nav"><span class="brand"><i class="brand-mark"></i>LogoPlaceholder</span><div class="menu"><span>Assessments</span><span class="on">Endorsement</span><span>Submissions</span><span>Results</span></div><span class="me" role="img" aria-label="User profile photo"></span><svg class="caret" viewBox="0 0 4 4"><path d="M.5 1.2 2 2.7 3.5 1.2" stroke="#fff" stroke-width=".6" fill="none"/></svg></header>
  <div class="abs crumb" style="left:25px;top:29px"><i class="back-ico"></i><b>Endorsement</b> / <b>New Endorsement Request</b> / Application Design Capabilities</div>
  <div class="abs h1" style="left:40px;top:44px"><i class="title-ico"></i>Application Design Capabilities</div>
  <div class="abs" style="left:0;right:0;top:63px;height:25px;background:var(--band)"></div>
  <div class="abs filter" style="left:39px;top:68px;width:135px">Choose Category<div class="field">Application Design Capabilities (24)<span style="margin-left:auto">⌄</span></div></div>
  <div class="abs filter" style="left:181px;top:68px;width:76px">Effective Date<div class="field">Select date<span style="margin-left:auto">⌄</span></div></div>
  <div class="abs filter" style="left:264px;top:68px;width:130px">Endorsement<div class="field" style="color:#9ca3af">Search<span style="margin-left:auto">⌕</span></div></div>
  <div class="abs filter" style="right:41px;top:78px;color:var(--primary)">Send Endorsement Request</div>
  <div class="abs body-soft" style="top:88px"></div>
  <div class="abs card" style="left:39px;top:102px;width:461px;height:190px">
    <div class="row head" style="grid-template-columns:10px 87px 160px 87px 1fr;height:17px"><i class="chk"></i><span>Endorsements</span><span>Skill &amp; Expertise</span><span>Role</span><span>Company</span></div>
    <div class="row" style="grid-template-columns:10px 87px 160px 87px 1fr 22px;height:20.5px"><i class="chk"></i><span style="display:flex;gap:4px;align-items:center"><i class="av" role="img" aria-label="Colleague photo"></i>Mei Lin Tan</span><span><i class="tag">UI</i><i class="tag">UX</i><i class="tag">Wireframe</i><i class="tag">Concept Design</i><i class="tag">Prototype</i></span><span>Fenwick Industries Ltd.</span><span class="link">Fenwick Industries Ltd.</span><i class="btn line" style="font-style:normal;height:10px;padding:0 5px">Add</i></div>
    <div class="row" style="grid-template-columns:10px 87px 160px 81px 1fr 28px;height:20.5px"><i class="chk"></i><span style="display:flex;gap:4px;align-items:center"><i class="av d" role="img" aria-label="Colleague photo"></i>Harold Dunne</span><span><i class="tag">Concept Design</i><i class="tag">Prototype</i></span><span>Brightcode Corp.</span><span class="link">Brightcode Corp.</span><i class="btn solid" style="font-style:normal;height:10px;padding:0 5px">Cancel</i></div>
    <div class="row" style="grid-template-columns:10px 87px 160px 87px 1fr 22px;height:20.5px"><i class="chk"></i><span style="display:flex;gap:4px;align-items:center"><i class="av g" role="img" aria-label="Colleague photo"></i>Marcus Tolland</span><span><i class="tag">UI</i><i class="tag">Design Analytic</i></span><span>Brightcode Corp.</span><span class="link">Brightcode Corp.</span><i class="btn line" style="font-style:normal;height:10px;padding:0 5px">Add</i></div>
    <div class="row" style="grid-template-columns:10px 87px 160px 87px 1fr 22px;height:20.5px"><i class="chk on"></i><span style="display:flex;gap:4px;align-items:center"><i class="av l" role="img" aria-label="Colleague photo"></i>Alina Kerr</span><span><i class="tag">Wireframe</i><i class="tag">Concept Design</i><i class="tag">Prototype</i></span><span>Brightcode Corp.</span><span class="link">Brightcode Corp.</span><i class="btn line" style="font-style:normal;height:10px;padding:0 5px">Add</i></div>
    <div class="row" style="grid-template-columns:10px 87px 160px 87px 1fr 22px;height:20.5px"><i class="chk"></i><span style="display:flex;gap:4px;align-items:center"><i class="av" role="img" aria-label="Colleague photo"></i>Rowan Marks Jr.</span><span><i class="tag">UX</i><i class="tag">Concept Design</i></span><span>Brightcode Corp.</span><span class="link">Brightcode Corp.</span><i class="btn line" style="font-style:normal;height:10px;padding:0 5px">Add</i></div>
    <div class="row" style="grid-template-columns:10px 87px 160px 87px 1fr 22px;height:20.5px"><i class="chk on"></i><span style="display:flex;gap:4px;align-items:center"><i class="av d" role="img" aria-label="Colleague photo"></i>Dimas R. Prakoso</span><span><i class="tag">Design Analytic</i><i class="tag">Wireframe</i></span><span>Inkara Studio</span><span class="link">Inkara Studio</span><i class="btn line" style="font-style:normal;height:10px;padding:0 5px">Add</i></div>
    <div class="row" style="grid-template-columns:10px 87px 160px 87px 1fr 22px;height:20.5px;border-bottom:0"><i class="chk"></i><span style="display:flex;gap:4px;align-items:center"><i class="av g" role="img" aria-label="Colleague photo"></i>Robin Clarke</span><span><i class="tag">Wireframe</i><i class="tag">UX</i><i class="tag">Concept Design</i><i class="tag">UI</i></span><span>Brightcode Corp.</span><span class="link">Brightcode Corp.</span><i class="btn line" style="font-style:normal;height:10px;padding:0 5px">Add</i></div>
    <div class="pager" style="margin-top:5px"><span>‹ Back</span><span class="cur">1</span><span class="plain">2</span><span>Next ›</span></div>
  </div>
</div></section>

<!-- ===== Submissions list ===== -->
<section class="screen" style="left:818px;top:106px"><div class="frame">
  <header class="nav"><span class="brand"><i class="brand-mark"></i>LogoPlaceholder</span><div class="menu"><span>Assessments</span><span>Endorsement</span><span class="on">Submissions</span><span>Results</span></div><span class="me" role="img" aria-label="User profile photo"></span><svg class="caret" viewBox="0 0 4 4"><path d="M.5 1.2 2 2.7 3.5 1.2" stroke="#fff" stroke-width=".6" fill="none"/></svg></header>
  <div class="abs crumb" style="left:32px;top:30px">Submissions /</div>
  <div class="abs h1" style="left:32px;top:42px">Submissions</div>
  <div class="abs sub" style="left:32px;top:58px">Here are the complete details of assessments.</div>
  <span class="abs btn solid" style="left:434px;top:47px;width:67px">⤒ Upload Documents</span>
  <div class="abs tabs" style="left:32px;top:75px;width:477px"><span class="on" style="width:40px">All (3)</span><span>Pending (2)</span></div>
  <div class="abs refresh" style="right:32px;top:75px">↻ Refresh</div>
  <div class="abs card" style="left:32px;top:102px;width:477px;height:126px">
    <div class="row head" style="grid-template-columns:124px 66px 63px 121px 1fr;height:18px"><span>File Name</span><span>Upload Date</span><span>File Format</span><span>Document Category</span><span>Status</span></div>
    <div class="row" style="grid-template-columns:124px 66px 63px 121px 1fr;height:27px"><span style="font-weight:500">Resume&amp;CV</span><span>23/02/2024</span><span>.ZIP</span><span>Resume</span><span style="display:flex;align-items:center"><i class="badge">Pending Review</i><i class="btn line" style="margin-left:auto;font-style:normal;height:11px">View</i></span></div>
    <div class="row" style="grid-template-columns:124px 66px 63px 121px 1fr;height:27px"><span style="font-weight:500">MyPortfolio_1</span><span>23/02/2024</span><span>.PDF</span><span>Portfolio</span><span style="display:flex;align-items:center"><i class="badge">Pending Review</i><i class="btn line" style="margin-left:auto;font-style:normal;height:11px">View</i></span></div>
    <div class="row" style="grid-template-columns:124px 66px 63px 121px 1fr;height:27px"><span style="font-weight:500">Curriculum Vitae</span><span>12/01/2024</span><span>.ZIP</span><span>Application</span><span style="display:flex;align-items:center;overflow:visible"><i class="badge teal">Approved</i><i class="dots" style="margin-left:auto;margin-right:8px;font-style:normal">⋮</i></span></div>
    <div class="pager" style="margin-top:8px"><span>‹ Back</span><span class="cur">1</span><span>Next ›</span></div>
  </div>
</div></section>

<!-- ===== Upload documents ===== -->
<section class="screen" style="left:818px;top:315px"><div class="frame">
  <header class="nav"><span class="brand"><i class="brand-mark"></i>LogoPlaceholder</span><div class="menu"><span>Assessments</span><span class="on">Endorsement</span><span>Submissions</span><span>Results</span></div><span class="me" role="img" aria-label="User profile photo"></span><svg class="caret" viewBox="0 0 4 4"><path d="M.5 1.2 2 2.7 3.5 1.2" stroke="#fff" stroke-width=".6" fill="none"/></svg></header>
  <div class="abs crumb" style="left:25px;top:29px"><i class="back-ico"></i><b>Submissions</b> / Upload Documents</div>
  <div class="abs h1" style="left:40px;top:44px"><i class="title-ico"></i>Upload Docuements</div>
  <div class="abs" style="left:0;right:0;top:64px;height:.6px;background:var(--line)"></div>
  <div class="abs body-soft" style="top:65px"></div>
  <div class="abs card" style="left:39px;top:73px;width:461px;height:161px;border-color:#eef0f3">
    <div class="abs filter" style="left:13px;top:12px;width:202px">Document Name<div class="field">MyPortfolio_2</div></div>
    <div class="abs filter" style="left:13px;top:40px;width:202px">Document Category<div class="field">Resume<span style="margin-left:auto">⌄</span></div></div>
    <div class="abs" style="left:13px;top:72px;width:202px;height:77px;border:.6px solid #d1d5db;border-radius:2px;background:#fafafa;text-align:center;font-size:3.6px;color:#6b7280">
      <div style="width:16px;height:16px;border-radius:50%;background:#e5e7eb;margin:18px auto 8px;display:flex;align-items:center;justify-content:center"><svg width="8" height="8" viewBox="0 0 8 8"><path d="M4 6V1.5M2.2 3.2 4 1.4l1.8 1.8M1 5.5v1.5h6V5.5" stroke="#6b7280" stroke-width=".6" fill="none"/></svg></div>
      Drag &amp; Drop here for upload<br>or <span class="link">browse file</span>
    </div>
    <div class="abs filter" style="left:246px;top:12px;width:202px">Note<div class="field" style="height:128px;align-items:flex-start;padding-top:4px;color:#9ca3af">Write here</div></div>
  </div>
  <span class="abs btn line" style="left:39px;top:260px;width:29px">Cancel</span>
  <span class="abs btn solid" style="left:446px;top:260px;width:54px">Submit Document</span>
</div></section>

</body>
</html>
```